Dental Practice Billboard Design

We are a newer dental practice in need of a simple but appealing billboard for our growing dental practice to attract new patients. The practice is owned by husband and wife dentists and is family friendly in a small town in Kentucky. We try to be very friendly and caring to our patients. Would prefer a blue background for the billboard and our tooth logo to be prominent. We are partial to the Patua One font used in the image below but please feel free to tweak it as you deem necessary. The shape of the uppercase D and lowercase g are why we like that font, so fonts with a similarly shaped “D” and “g” would work as well. Please include our phone number (555) 847-1390. Please see our website Harlowbrookdentistry.example for more info on the practice if needed. Thank you! Looking forward to seeing your creation.
Updates

The dimensions will be 12ft x 24ft (3.6576m x 7.3152m). Apologies for not including this in the original prompt. Thank you all for your submissions.

Industry/Entity Type

Dental

Font styles to use
Other font styles liked:
• Patua One

Colors
0054AA
0677BA
7BADD7
CADEEF
E8F1F8
0094D4
00A9DD
6FCCEA
C7EBF8
E9F6FB
00AB8E
00BBA5
67D7C9
C6EFE9
E9F9F6
59FF00
82FF00
B8FF75
E3FFCB
F4FFEA

Requirements
Must have
• Phone number, website, Logo, Practice name “Harlow Brook Dentistry”
Should not have
• A tagline or slogan

```html
<!DOCTYPE html>
<html lang="en">
<head>
<meta charset="utf-8">
<title>Harlow Brook Dentistry – Billboard</title>
<link rel="stylesheet" href="https://fonts.googleapis.com/css2?family=Patua+One&family=Montserrat:wght@700&display=swap">
<style>
  :root {
    --page-bg: #e8edf2;
    --board-navy: #012a5c;
    --band-blue: #0057c2;
    --band-line: #2f7be0;
    --accent-green: #19b31a;
    --ink-white: #ffffff;
  }
  * { margin: 0; padding: 0; box-sizing: border-box; }
  html, body {
    width: 1200px;
    height: 730px;
    overflow: hidden;
    background: var(--page-bg);
  }
  .billboard {
    position: absolute;
    left: 20px;
    top: 75px;
    width: 1160px;
    height: 580px;
    background: var(--board-navy);
    overflow: hidden;
    color: var(--ink-white);
    font-family: "Patua One", Georgia, serif;
  }
  .billboard-waves {
    position: absolute;
    inset: 0;
    width: 100%;
    height: 100%;
  }
  .logo-mark {
    position: absolute;
    left: 40px;
    top: 70px;
    width: 290px;
    height: 290px;
    display: flex;
    flex-direction: column;
    align-items: center;
    justify-content: center;
    gap: 18px;
  }
  .logo-dot {
    width: 70px;
    height: 70px;
    border-radius: 50%;
    background: var(--accent-green);
  }
  .logo-name {
    font-size: 40px;
    line-height: 1;
    color: var(--ink-white);
    text-align: center;
  }
  .practice-name {
    position: absolute;
    left: 370px;
    top: 40px;
    line-height: 1;
  }
  .practice-name .name-main {
    display: block;
    font-size: 150px;
    letter-spacing: 1px;
  }
  .practice-name .name-sub {
    display: block;
    font-size: 74px;
    margin-top: 8px;
    margin-left: -14px;
  }
  .contact {
    position: absolute;
    right: 48px;
    bottom: 40px;
    text-align: right;
  }
  .contact-line {
    display: flex;
    align-items: center;
    justify-content: flex-end;
    gap: 10px;
  }
  .contact-phone {
    font-family: "Montserrat", Arial, sans-serif;
    font-weight: 700;
    font-size: 46px;
    letter-spacing: 1px;
  }
  .contact-web {
    font-size: 30px;
    margin-top: 4px;
  }
  .contact-icon { flex: none; }
</style>
</head>
<body>
  <section class="billboard" aria-label="Harlow Brook Dentistry billboard">
    <svg class="billboard-waves" viewBox="0 0 1160 580" preserveAspectRatio="none" aria-hidden="true">
      <path fill="var(--ink-white)" d="M360 580 C 640 470, 860 345, 1160 335 L1160 580 Z"/>
      <path fill="var(--board-navy)" d="M360 580 C 650 495, 860 372, 1160 368 L1160 580 Z"/>
      <path fill="var(--band-blue)" d="M0 540 C 380 600, 720 405, 1160 392 L1160 580 L0 580 Z"/>
      <path fill="none" stroke="var(--ink-white)" stroke-width="4" d="M200 570 C 560 540, 780 400, 1080 410"/>
      <path fill="var(--accent-green)" d="M0 400 C 90 500, 270 555, 540 490 C 300 570, 100 545, 0 470 Z"/>
    </svg>

    <div class="logo-mark">
      <span class="logo-dot"></span>
      <span class="logo-name">Harlow Brook</span>
    </div>

    <h1 class="practice-name">
      <span class="name-main">Harlow</span>
      <span class="name-sub">Brook Dentistry</span>
    </h1>

    <div class="contact">
      <div class="contact-line contact-phone">
        <svg class="contact-icon" width="34" height="34" viewBox="0 0 24 24" aria-hidden="true">
          <path fill="var(--ink-white)" d="M6.6 10.8a15.1 15.1 0 0 0 6.6 6.6l2.2-2.2c.3-.3.7-.4 1-.2 1.1.4 2.3.6 3.6.6.6 0 1 .4 1 1V20c0 .6-.4 1-1 1A17 17 0 0 1 3 4c0-.6.4-1 1-1h3.5c.6 0 1 .4 1 1 0 1.3.2 2.5.6 3.6.1.3 0 .7-.2 1z"/>
        </svg>
        <span>(555) 847-1390</span>
      </div>
      <div class="contact-line contact-web">
        <svg class="contact-icon" width="30" height="30" viewBox="0 0 24 24" aria-hidden="true">
          <g fill="none" stroke="var(--ink-white)" stroke-width="1.8">
            <circle cx="12" cy="12" r="10"/>
            <ellipse cx="12" cy="12" rx="4.5" ry="10"/>
            <path d="M2 12h20M4 7h16M4 17h16"/>
          </g>
        </svg>
        <span>Harlowbrookdentistry.example</span>
      </div>
    </div>
  </section>
</body>
</html>
```